Business Cards for new orthopaedic surgery practice

My husband and I are starting our own orthopaedic surgery practice. We are looking for a business card that is uniform, but one will have my name/title and the other will have his. You can just create one design with my name on it for now. But when I choose your design as the winning design I will ask that you add another copy with his name/title.

We are looking for classy, simple, elite all in one. We like dark blues/a little gold/yellow. Something that goes with our logo. We want our logo incorporated. Here is all the info you need:
Business name: RV Bone & Vitality Center
Location: 38517 North Willowmere Ave
Maple Hollow, FL 33409
Phone: 954-218-4063
Fax: 954-582-7341
Email: info@myrvbonecare.example

Names: Lydia Vance, M.D.
Board Certified Hand and Upper Extremity Surgeon

Ebo Dansu, M.D.
Board Certified Hip & Knee Replacement/General Orthopaedic Surgeon

Can decide what you want to put on the back. Maybe a slogan:
Grounded in Care. Centered on You

I am just going to upload our logo. The only thing is if we select you as the winning design, the location, and phone numbers may change. We will need your help to update that once fully solidified.

Industry/Entity Type

Medical

Contact Information for Business Card

Colors
0054AA
0677BA
7BADD7
CADEEF
E8F1F8
0094D4
00A9DD
6FCCEA
C7EBF8
E9F6FB

Requirements
Must have
• class, appeal,
Should not have
• We want to air on the side of masculine if we are looking at masculine vs. feminine feel. But we still want it classy, sophisticated, and something we will love

```html
<!DOCTYPE html>
<html lang="en">
<head>
<meta charset="utf-8">
<title>RV Bone &amp; Vitality Center – Business Card</title>
<link rel="stylesheet" href="https://fonts.googleapis.com/css2?family=Libre+Baskerville:wght@400;700&family=Arimo:wght@400&display=swap">
<style>
  :root {
    --page: #e4e4e4;
    --paper: #ffffff;
    --navy: #1f2e5a;
    --navy-top: #283a6a;
    --navy-bottom: #1c2850;
    --gold: #c9a86a;
    --text-grey: #555a63;
  }
  * { margin: 0; padding: 0; box-sizing: border-box; }
  html, body { width: 1200px; height: 1200px; overflow: hidden; }
  body { background: var(--page); position: relative; font-family: "Arimo", Arial, sans-serif; }

  .card { position: absolute; width: 688px; height: 393px; overflow: hidden; }
  .card--front { left: 267px; top: 159px; background: var(--paper); }
  .card--back {
    left: 262px; top: 653px;
    background: linear-gradient(180deg, var(--navy-top), var(--navy-bottom));
  }

  .badge {
    position: absolute; left: 57px; top: 158px;
    width: 146px; height: 146px; border-radius: 50%;
    border: 1.5px solid var(--gold);
    display: flex; align-items: center; justify-content: center;
    text-align: center;
  }
  .badge__name {
    font-family: "Libre Baskerville", Georgia, serif; font-weight: 700;
    color: var(--navy); font-size: 15px; line-height: 1.35;
  }

  .details { position: absolute; right: 43px; top: 78px; text-align: right; }
  .details__name {
    font-family: "Libre Baskerville", Georgia, serif; font-weight: 700;
    color: var(--navy); font-size: 21px; letter-spacing: 0.5px;
  }
  .details__title { color: var(--gold); font-size: 15.5px; line-height: 20px; margin-top: 6px; }
  .details__address { color: var(--text-grey); font-size: 16px; line-height: 21px; margin-top: 17px; }
  .contact { list-style: none; margin-top: 12px; }
  .contact li {
    color: var(--text-grey); font-size: 16px; line-height: 20.5px;
    display: flex; justify-content: flex-end; align-items: center; gap: 7px;
  }
  .contact svg { width: 14px; height: 14px; fill: var(--navy); flex: none; }

  .back-name {
    position: absolute; left: 0; right: 0; top: 160px; text-align: center;
    font-family: "Libre Baskerville", Georgia, serif; font-weight: 700;
    color: #ffffff; font-size: 34px;
  }
  .slogan {
    position: absolute; left: 0; right: 0; top: 302px; text-align: center;
    color: var(--gold); font-size: 16px; letter-spacing: 3.4px;
  }
</style>
</head>
<body>
  <section class="card card--front">
    <div class="badge"><span class="badge__name">RV Bone &amp;<br>Vitality<br>Center</span></div>
    <div class="details">
      <h1 class="details__name">LYDIA VANCE, M.D.</h1>
      <p class="details__title">Board Certified Hand and<br>Upper Extremity Surgeon</p>
      <p class="details__address">38517 North Willowmere Ave<br>Maple Hollow, FL 33409</p>
      <ul class="contact">
        <li>954-218-4063
          <svg viewBox="0 0 24 24" aria-label="Phone"><path d="M6.6 10.8a15.2 15.2 0 0 0 6.6 6.6l2.2-2.2c.3-.3.7-.4 1-.2 1.1.4 2.3.6 3.6.6.6 0 1 .4 1 1V20c0 .6-.4 1-1 1A17 17 0 0 1 3 4c0-.6.4-1 1-1h3.5c.6 0 1 .4 1 1 0 1.3.2 2.5.6 3.6.1.3 0 .7-.2 1z"/></svg></li>
        <li>954-582-7341
          <svg viewBox="0 0 24 24" aria-label="Fax"><path d="M6 2h9l3 3v4H6zM3 10h18v9H3zM6 16h12v6H6z"/></svg></li>
        <li>info@myrvbonecare.example
          <svg viewBox="0 0 24 24" aria-label="Email"><path d="M2 5h20v14H2zM3.5 6.5 12 13l8.5-6.5v-.2H3.5z" fill-rule="evenodd"/></svg></li>
        <li>www.myrvbonecare.example
          <svg viewBox="0 0 24 24" aria-label="Website"><circle cx="12" cy="12" r="10"/><path d="M12 2v20M2 12h20" stroke="#fff" stroke-width="1.5"/></svg></li>
      </ul>
    </div>
  </section>

  <section class="card card--back">
    <h2 class="back-name">RV Bone &amp; Vitality Center</h2>
    <p class="slogan">GROUNDED IN CARE. CENTERED ON YOU</p>
  </section>
</body>
</html>
```